Animal Eye Clinic needs a Business card

We are a new veterinary ophthalmology practice (Ridgeline Pet Vision Care) and we need a business card designed. We only see animal eyes - we are not a regular veterinary clinic. We already have a logo. We are looking for a professional, good looking business card to hand out to our clients. We are looking for something simple but professional and contemporary. Our logo is likely the only picture/graphic that needs to be on the card.
Updates

Contact Information for Business Card

Delia Vossman, BSc, DVM, MSc, DipACVO
Veterinary Ophthalmologist

Phone: 250.418.3927
Email: ridgelinepetvisioncare@mailbox-example.net
Website: ridgelinepetvisioncare-example.net
Address: 1874 Thornbury Rd
Kelowna, BC, V1X 4M9

Colors

Designer to choose colors to be used in the design.

Requirements
Must have
• Our logo (attached)

```html
<!DOCTYPE html>
<html lang="en">
<head>
<meta charset="utf-8">
<title>Ridgeline Pet Vision Care – Business Card</title>
<link rel="stylesheet" href="https://fonts.googleapis.com/css2?family=Roboto:wght@400;500;700&display=swap">
<style>
  :root {
    --teal: #1b97a8;
    --teal-dark: #157f8e;
    --slate: #6b6b6b;
    --ink: #555a5e;
    --paper: #ffffff;
    --backdrop: #d3d6d9;
  }
  * { box-sizing: border-box; margin: 0; padding: 0; }
  html, body { width: 1200px; height: 800px; overflow: hidden; }
  body {
    background: var(--backdrop);
    font-family: "Roboto", Arial, sans-serif;
    position: relative;
  }
  .card {
    position: absolute;
    width: 580px;
    height: 332px;
    background: var(--paper);
    box-shadow: 0 6px 18px rgba(0,0,0,.18);
    overflow: hidden;
  }
  .card-front { left: 310px; top: 46px; }
  .card-back  { left: 310px; top: 418px; }

  /* Front */
  .front-brand {
    position: absolute;
    left: 0; right: 0; top: 110px;
    display: flex; align-items: center; justify-content: center; gap: 14px;
  }
  .brand-dot {
    width: 34px; height: 34px; border-radius: 50%;
    background: var(--teal);
    flex: none;
  }
  .brand-name {
    color: var(--teal);
    font-weight: 700;
    font-size: 30px;
    letter-spacing: .5px;
    text-transform: uppercase;
    line-height: 1.05;
    text-align: left;
  }
  .front-web {
    position: absolute;
    left: 0; right: 0; bottom: 62px;
    text-align: center;
    color: var(--ink);
    font-size: 15px;
    letter-spacing: 2px;
  }

  /* Back */
  .back-band { position: absolute; inset: 0; }
  .holder {
    position: absolute; left: 24px; top: 22px;
    color: #fff;
  }
  .holder-name { font-weight: 700; font-size: 20px; text-transform: uppercase; letter-spacing: .3px; }
  .holder-creds { font-weight: 500; font-size: 13px; margin-top: 3px; }
  .holder-title { font-size: 14px; margin-top: 2px; }

  .back-brand {
    position: absolute; right: 26px; top: 70px;
    color: var(--teal); font-weight: 700; font-size: 22px;
    text-transform: uppercase; text-align: right; line-height: 1.1;
  }
  .contact {
    position: absolute; right: 26px; bottom: 20px;
    text-align: right; color: var(--ink); font-size: 13px; line-height: 1.45;
  }
  .address { margin-bottom: 12px; }
  .contact-line { display: flex; justify-content: flex-end; align-items: center; gap: 7px; white-space: nowrap; }
  .contact-line svg { width: 14px; height: 14px; flex: none; }
</style>
</head>
<body>

<section class="card card-front" aria-label="Business card front">
  <div class="front-brand">
    <span class="brand-dot"></span>
    <span class="brand-name">Ridgeline<br>Pet Vision Care</span>
  </div>
  <p class="front-web">ridgelinepetvisioncare-example.net</p>
</section>

<section class="card card-back" aria-label="Business card back">
  <svg class="back-band" width="580" height="332" viewBox="0 0 580 332">
    <defs>
      <linearGradient id="illo" x1="0" y1="0" x2="1" y2="1">
        <stop offset="0" stop-color="#1b97a8"/>
        <stop offset="1" stop-color="#6b6b6b"/>
      </linearGradient>
    </defs>
    <polygon points="0,0 300,0 285,140 225,332 0,332" fill="var(--teal)"/>
    <rect x="20" y="150" width="190" height="182" fill="url(#illo)" role="img"
          aria-label="Silhouettes of a dog, a cat and a horse"/>
  </svg>

  <div class="holder">
    <p class="holder-name">Delia Vossman</p>
    <p class="holder-creds">BSc, DVM, MSc, DipACVO</p>
    <p class="holder-title">Veterinary Ophthalmologist</p>
  </div>

  <p class="back-brand">Ridgeline<br>Pet Vision Care</p>

  <div class="contact">
    <p class="address">1874 Thornbury Rd<br>Kelowna, BC, V1X 4M9</p>
    <p class="contact-line">250.418.3927
      <svg viewBox="0 0 24 24"><path fill="var(--teal)" d="M6.6 10.8a15 15 0 0 0 6.6 6.6l2.2-2.2c.3-.3.7-.4 1-.2 1.1.4 2.3.6 3.6.6.6 0 1 .4 1 1V20c0 .6-.4 1-1 1A17 17 0 0 1 3 4c0-.6.4-1 1-1h3.5c.6 0 1 .4 1 1 0 1.3.2 2.5.6 3.6.1.3 0 .7-.2 1z"/></svg>
    </p>
    <p class="contact-line">ridgelinepetvisioncare@mailbox-example.net
      <svg viewBox="0 0 24 24"><rect x="3" y="5" width="18" height="14" fill="none" stroke="var(--teal)" stroke-width="2"/><path d="M3 6l9 7 9-7" fill="none" stroke="var(--teal)" stroke-width="2"/></svg>
    </p>
    <p class="contact-line">ridgelinepetvisioncare-example.net
      <svg viewBox="0 0 24 24"><circle cx="12" cy="12" r="9" fill="none" stroke="var(--teal)" stroke-width="2"/><path d="M3 12h18M12 3c3 3 3 15 0 18M12 3c-3 3-3 15 0 18" fill="none" stroke="var(--teal)" stroke-width="1.6"/></svg>
    </p>
  </div>
</section>

</body>
</html>
```